Presentation and Communication Coaching Services Business needs updated interactive web site

I want to keep the color scheme, functionality, and pages of my current site, but with a newer/updated look. I need to improve security and simplify images, etc. (Please see current site http://brightwellvoicetutor.com ) This will need be functional on mobile devices, as well.

I'm attached to the scrolling client list and scrolling client feedback.

Industry/Entity Type

Professional Service

Font styles to use
Sans Serif

Colors
0356a4
f37122
33a6d7

Requirements
Must have
• scrolling client banner on home page, client comments slider, color scheme
• Please see current site: http://brightwellvoicetutor.com
Nice to have
• better action/appearance
Should not have
• I don't want it to look like all the other sites/templates

```html
<!DOCTYPE html>
<html lang="en">
<head>
<meta charset="utf-8">
<title>Brightwell Voice Tutoring</title>
<link href="https://fonts.googleapis.com/css2?family=Montserrat:wght@400;500;600;700&family=Open+Sans:ital,wght@0,400;0,600;1,400&display=swap" rel="stylesheet">
<style>
:root{
  --navy:#173a55;
  --navy-deep:#122f47;
  --teal:#1e5678;
  --blue:#33a6d7;
  --gold:#e9b234;
  --white:#ffffff;
  --soft:#c9d8e4;
  --muted:#8fa9bd;
}
*{margin:0;padding:0;box-sizing:border-box}
html,body{width:1200px;height:3390px;overflow:hidden}
body{position:relative;background:var(--navy);color:var(--white);font-family:"Open Sans",Arial,sans-serif}
.abs{position:absolute}
h1,h2,h3,.heading{font-family:"Montserrat",Arial,sans-serif;font-weight:500}

/* hero */
.hero{left:0;top:0;width:1200px;height:855px;background:radial-gradient(ellipse at 30% 55%,#2c5674 0%,#1a3d58 55%,#14324b 100%)}
.hero-photo{left:0;top:150px;width:560px;height:705px;background:radial-gradient(ellipse at 40% 50%,rgba(80,120,150,.45),rgba(20,50,75,0) 70%)}
.mic-glow{left:300px;top:120px;width:260px;height:260px;border-radius:50%;background:radial-gradient(circle,rgba(90,140,170,.5),rgba(20,50,75,0) 70%)}
.brand{left:150px;top:22px;font-family:"Montserrat",sans-serif;font-size:25px;font-weight:500;letter-spacing:-.3px;color:var(--white)}
.brand span{color:var(--gold)}
.socials{display:flex;gap:10px}
.social{width:27px;height:27px;border-radius:50%;border:1.5px solid var(--muted);background:rgba(255,255,255,.05)}
.social.on{background:var(--blue);border-color:var(--blue)}
.header-socials{left:562px;top:22px}
.btn{display:inline-flex;align-items:center;justify-content:center;border-radius:20px;font-family:"Montserrat",sans-serif;font-weight:600;font-size:12px}
.btn-gold{background:var(--gold);color:var(--navy-deep)}
.btn-blue{background:var(--blue);color:var(--white)}
.register-top{left:765px;top:20px;width:135px;height:32px}
.login-top{left:915px;top:20px;width:136px;height:32px}
.nav{left:150px;top:82px;width:900px;display:flex;justify-content:space-between;font-family:"Montserrat",sans-serif;font-size:11px;font-weight:600;letter-spacing:1px}
.nav .active{color:var(--blue)}
.quote{left:330px;top:225px;width:590px;text-align:center;font-style:italic;font-size:17px;line-height:27px;color:var(--white)}
.quote b{color:var(--gold);font-weight:700}
.dots{left:565px;top:393px;display:flex;gap:7px}
.dots i{width:8px;height:8px;border-radius:50%;border:1px solid var(--muted)}
.dots i.on{background:var(--muted)}
.hero-title{left:637px;top:487px;font-size:30px;line-height:36px;color:var(--gold)}
.hero-text{left:637px;top:570px;width:410px;font-size:11px;line-height:18px;color:var(--soft)}
.hero-text p+p{margin-top:12px}

/* clients */
.clients{left:0;top:855px;width:1200px;height:100px;background:#13314a;display:flex;align-items:center;justify-content:space-around;padding:0 60px}
.client{font-family:"Montserrat",sans-serif;font-weight:500;font-size:18px;color:#dfe8ef;display:flex;align-items:center;gap:8px}
.client i{width:14px;height:14px;border-radius:50%;background:#dfe8ef}

/* approach */
.approach{left:0;top:955px;width:1200px;height:500px;background:linear-gradient(100deg,#1b4361 0%,#1f4c6c 55%,#2d5c7a 80%,#1c4563 100%)}
.approach-photo{left:760px;top:955px;width:440px;height:420px;background:radial-gradient(ellipse at 50% 40%,rgba(150,170,185,.35),rgba(30,70,100,0) 70%)}
.step{width:220px;text-align:center}
.step .circle{width:110px;height:110px;border-radius:50%;background:var(--gold);margin:0 auto;display:flex;align-items:center;justify-content:center}
.step .circle.white{background:var(--white)}
.step h3{margin-top:28px;font-size:16px;font-weight:600}
.step.current h3{color:var(--gold)}
.step p{margin-top:10px;font-size:11.5px;line-height:17px;color:var(--soft)}
.section-title{width:1200px;left:0;text-align:center;font-size:28px;color:var(--gold)}

/* services */
.tile{overflow:hidden}
.tile-img{width:100%;height:100%}
.tile-body{position:absolute;left:75px;top:72px;width:560px}
.tile h3{font-size:17px;color:var(--gold);font-weight:500}
.tile p{margin-top:8px;font-size:11.5px;line-height:17px;color:var(--soft)}
.more{margin-top:18px;width:58px;height:26px;border-radius:14px;font-size:10px;background:rgba(255,255,255,.15);color:var(--white)}
.more.blue{background:var(--blue)}

/* signup */
.signup{left:0;top:1975px;width:1200px;height:115px;background:var(--gold)}
.signup-text{left:150px;top:36px;width:430px;font-family:"Montserrat",sans-serif;font-weight:600;font-size:16px;line-height:22px;color:var(--navy-deep)}
.signup-field{left:600px;top:34px;width:450px;height:46px;border:1.5px solid #8c6a1c;border-radius:24px}
.signup-field span{position:absolute;left:22px;top:13px;font-size:13px;color:#7a5d1a}
.signup-btn{position:absolute;right:-2px;top:-2px;width:178px;height:47px;background:var(--teal);color:var(--white);font-size:13px}

/* publications */
.pubs{left:0;top:2090px;width:1200px;height:1006px;background:linear-gradient(180deg,#1e5a80 0%,#1b4d6e 45%,#173f5c 100%)}
.cover{box-shadow:8px 10px 18px rgba(0,0,0,.35)}
.caption{width:240px;text-align:center;font-size:12.5px;line-height:18px}
.subtitle{left:0;top:2682px;width:1200px;text-align:center;font-size:13px}
.subtitle em{font-style:normal;color:var(--blue)}
.tips{left:149px;top:2728px;list-style:none;font-size:11.5px;line-height:22.7px;color:var(--soft)}
.tips li{display:flex;align-items:center;gap:10px}
.video{left:599px;top:2730px;width:452px;height:303px;background:linear-gradient(135deg,#a9714f 0%,#8a5b44 45%,#5b3f33 100%)}
.play{left:805px;top:2862px}

/* footer */
.footer{left:0;top:3096px;width:1200px;height:249px;background:#16364f}
.footer-name{left:150px;top:3120px;font-size:27px;color:var(--gold)}
.footer-role{left:150px;top:3155px;font-size:12px;color:var(--soft)}
.footer-about{left:150px;top:3190px;width:380px;font-size:11.5px;line-height:17px;color:var(--muted)}
.consult{left:150px;top:3278px;width:118px;height:28px;border:1.5px solid var(--muted);color:var(--muted);font-size:10px}
.call{left:637px;top:3118px;font-size:27px;color:var(--blue);font-weight:400}
.email{left:637px;top:3152px;font-size:12px}
.footer-socials{left:637px;top:3190px}
.register-foot{left:840px;top:3188px;width:122px;height:28px}
.footer-links{left:637px;top:3283px;font-size:11px;color:var(--soft);display:flex;gap:18px}
.to-top{left:1110px;top:3122px}
.copyright{left:0;top:3345px;width:1200px;height:45px;background:#102a3f;font-size:11px;color:var(--muted);padding:16px 150px}
</style>
</head>
<body>

<section class="abs hero" aria-label="Welcome">
  <div class="abs hero-photo" role="img" aria-label="Speaker holding a microphone in front of an audience"></div>
  <div class="abs mic-glow" role="img" aria-label="Microphone in soft light"></div>
</section>

<header>
  <div class="abs brand">brightwell<span>voicetutoring</span></div>
  <div class="abs socials header-socials">
    <i class="social"></i><i class="social on"></i><i class="social"></i><i class="social"></i><i class="social"></i>
  </div>
  <a class="abs btn btn-gold register-top">Register Now!</a>
  <a class="abs btn btn-blue login-top">Client Login</a>
  <nav class="abs nav">
    <span class="active">HOME</span><span>ABOUT</span><span>CLIENTS</span><span>REVIEWS</span><span>SERVICES</span><span>CONTACT</span><span>SPEAKING SECRETS</span>
  </nav>
</header>

<blockquote class="abs quote">I was the first to present and they were really interested in some of the key stuff, they were throwing questions left/right. Ended up being up on the stage for 1 hour and 10 min! It was really great! <b>”</b></blockquote>
<div class="abs dots"><i class="on"></i><i></i><i></i><i></i><i></i></div>

<h1 class="abs hero-title">You’re good at what you do.<br>Learn How to let it show.</h1>
<div class="abs hero-text">
  <p>An individual works hard to reach a place of respect and authority in her or his chosen profession. Effective self-presentation adds confidence and allows one’s unique personality and expertise to shine through – in fact, it is key in separating from the pack and reaching higher goals. As competition increases, these skills become more essential in demonstrating value to an employer, manager, or board.</p>
  <p>You’ve done your best to reach this professional level. It’s time to develop what it takes to reach the next one.</p>
</div>

<div class="abs clients" aria-label="Clients">
  <span class="client"><i></i>Northgate</span>
  <span class="client">Clearpath</span>
  <span class="client">Lumina</span>
  <span class="client">Rivermark</span>
  <span class="client">Veltro</span>
  <span class="client">Harlow + Finch</span>
</div>

<section class="abs approach" aria-label="Approach"></section>
<div class="abs approach-photo" role="img" aria-label="Smiling professional woman"></div>

<div class="abs step" style="left:152px;top:1052px">
  <div class="circle"><svg width="46" height="46" viewBox="0 0 46 46" fill="none" stroke="#fff" stroke-width="3"><path d="M13 6h20v12a10 10 0 0 1-20 0z"/><path d="M13 10H6v4a7 7 0 0 0 7 7M33 10h7v4a7 7 0 0 1-7 7"/><path d="M23 28v8M15 40h16"/></svg></div>
  <h3>The Goal</h3>
</div>
<div class="abs step current" style="left:376px;top:1052px">
  <div class="circle white"><svg width="46" height="46" viewBox="0 0 46 46" fill="none" stroke="#e9b234" stroke-width="3"><circle cx="17" cy="27" r="8"/><circle cx="17" cy="27" r="2.5"/><circle cx="32" cy="14" r="6"/><circle cx="32" cy="14" r="2"/><path d="M17 15v4M17 35v4M5 27h4M25 27h4M32 4v4M32 20v4M22 14h4M38 14h4"/></svg></div>
  <h3>The Challenge</h3>
  <p>Find a path to develop skills and strategies to accomplish this aim while also projecting confidence, warmth, and credibility.</p>
</div>
<div class="abs step" style="left:602px;top:1052px">
  <div class="circle"><svg width="46" height="46" viewBox="0 0 46 46" fill="none" stroke="#fff" stroke-width="3"><path d="M10 12h9a4 4 0 1 1 8 0h9v9a4 4 0 1 0 0 8v9h-9a4 4 0 1 0-8 0h-9v-9a4 4 0 1 1 0-8z"/></svg></div>
  <h3>The Solution</h3>
</div>
<div class="abs step" style="left:826px;top:1052px">
  <div class="circle"><svg width="46" height="46" viewBox="0 0 46 46" fill="none" stroke="#fff" stroke-width="3"><rect x="6" y="8" width="34" height="30"/><path d="M10 32l9-10 7 6 10-12"/></svg></div>
  <h3>The Result</h3>
</div>

<h2 class="abs section-title" style="top:1375px">Services We Provide</h2>

<article class="abs tile" style="left:0;top:1451px;width:714px;height:262px">
  <div class="tile-img" role="img" aria-label="Coach presenting to a small group" style="background:linear-gradient(90deg,#3d7596 0%,#5f93b0 45%,#8fb5c9 75%,#5b84a0 100%)"></div>
  <div class="tile-body" style="top:78px">
    <h3>Coaching</h3>
    <p>One-on-one, individual and customized to your unique goals, obstacles, and challenges. In person, or via video conference.</p>
    <a class="btn more">More</a>
  </div>
</article>
<article class="abs tile" style="left:714px;top:1451px;width:486px;height:262px">
  <div class="tile-img" role="img" aria-label="Executives in a meeting" style="background:linear-gradient(90deg,#1f4f70 0%,#356a8a 50%,#7a98ad 100%)"></div>
  <div class="tile-body" style="left:72px;top:70px;width:300px">
    <h3>Accents</h3>
    <p>Support for executives from outside the U.S. to increase intelligibility and diminish obstacles to successful communication in American English.</p>
    <a class="btn more">More</a>
  </div>
</article>
<article class="abs tile" style="left:0;top:1713px;width:488px;height:262px">
  <div class="tile-img" role="img" aria-label="Workshop audience" style="background:linear-gradient(90deg,#275d80 0%,#2f688a 60%,#1e4a68 100%)"></div>
  <div class="tile-body" style="top:70px;width:340px">
    <h3>Custom Workshops</h3>
    <p>Unique, effective program design and facilitation to match the needs of executives, managers, or promising individuals of any level.</p>
    <a class="btn more blue">More</a>
  </div>
</article>
<article class="abs tile" style="left:488px;top:1713px;width:712px;height:262px">
  <div class="tile-img" role="img" aria-label="Notebook and pen on a desk" style="background:linear-gradient(90deg,#5a5f63 0%,#4a5459 50%,#3a4c58 100%)"></div>
  <div class="tile-body" style="left:75px;top:76px;width:560px">
    <h3>Keynote Speeches</h3>
    <p>Fresh ways of thinking about speaking and communication combined with practical tools for participants of your next conference or event.</p>
    <a class="btn more" style="background:transparent">More</a>
  </div>
</article>

<section class="abs signup" aria-label="Sign up">
  <p class="abs signup-text">Register and receive FREE “7 Keys to Confident Speaking”</p>
  <div class="abs signup-field"><span>name@email.com</span><a class="btn signup-btn">Register Now!</a></div>
</section>

<section class="abs pubs" aria-label="Publications"></section>
<h2 class="abs section-title" style="top:2140px">Recent Publications</h2>

<div class="abs cover" role="img" aria-label="Gentry Quarterly magazine cover" style="left:262px;top:2203px;width:210px;height:295px;background:linear-gradient(160deg,#3b8fd0,#1f5fa8 60%,#e1c23a)"></div>
<div class="abs cover" role="img" aria-label="Maison Belle magazine cover" style="left:488px;top:2203px;width:175px;height:295px;background:linear-gradient(160deg,#d8dde3,#a5b6c4 50%,#6b8aa2)"></div>
<div class="abs cover" role="img" aria-label="Metro Daily feature photo" style="left:712px;top:2218px;width:225px;height:265px;background:linear-gradient(180deg,#b0462f 0%,#8a3324 50%,#2b2a30 100%)"></div>
<p class="abs caption" style="left:247px;top:2517px">Spring/Summer Gentry Quarterly<br>Style Almanac</p>
<p class="abs caption" style="left:455px;top:2517px">Maison Belle<br>Magazine</p>
<p class="abs caption" style="left:705px;top:2517px">Metro Daily<br>Feature</p>

<h2 class="abs section-title" style="top:2626px">BVT Provides Training, Tools, and Techniques</h2>
<p class="abs subtitle">Watch A <em>Free Video</em> With 5 Great Speaking Tips</p>

<ul class="abs tips">
  <li><svg width="12" height="12" viewBox="0 0 12 12" fill="none" stroke="#c9d8e4"><circle cx="6" cy="6" r="5.3"/><path d="M3.5 6.2l1.8 1.7 3.2-3.6"/></svg>Executive Presence – Polishing Personal Presentation/Manner</li>
  <li><svg width="12" height="12" viewBox="0 0 12 12" fill="none" stroke="#c9d8e4"><circle cx="6" cy="6" r="5.3"/><path d="M3.5 6.2l1.8 1.7 3.2-3.6"/></svg>Addressing and Overcoming Speaking/Communication</li>
  <li style="padding-left:22px">Anxiety</li>
  <li><svg width="12" height="12" viewBox="0 0 12 12" fill="none" stroke="#c9d8e4"><circle cx="6" cy="6" r="5.3"/><path d="M3.5 6.2l1.8 1.7 3.2-3.6"/></svg>Last-Minute Presentation 911</li>
  <li><svg width="12" height="12" viewBox="0 0 12 12" fill="none" stroke="#c9d8e4"><circle cx="6" cy="6" r="5.3"/><path d="M3.5 6.2l1.8 1.7 3.2-3.6"/></svg>Media Training</li>
  <li><svg width="12" height="12" viewBox="0 0 12 12" fill="none" stroke="#c9d8e4"><circle cx="6" cy="6" r="5.3"/><path d="M3.5 6.2l1.8 1.7 3.2-3.6"/></svg>Modifying Accents for Clarity and Intelligibility</li>
  <li><svg width="12" height="12" viewBox="0 0 12 12" fill="none" stroke="#c9d8e4"><circle cx="6" cy="6" r="5.3"/><path d="M3.5 6.2l1.8 1.7 3.2-3.6"/></svg>Communicating Complex/Technical Material to Any Audience</li>
  <li><svg width="12" height="12" viewBox="0 0 12 12" fill="none" stroke="#c9d8e4"><circle cx="6" cy="6" r="5.3"/><path d="M3.5 6.2l1.8 1.7 3.2-3.6"/></svg>Cultivating a More Effective Communication Style</li>
  <li><svg width="12" height="12" viewBox="0 0 12 12" fill="none" stroke="#c9d8e4"><circle cx="6" cy="6" r="5.3"/><path d="M3.5 6.2l1.8 1.7 3.2-3.6"/></svg>Incorporating and Interacting with Audio/Visual Aids</li>
  <li><svg width="12" height="12" viewBox="0 0 12 12" fill="none" stroke="#c9d8e4"><circle cx="6" cy="6" r="5.3"/><path d="M3.5 6.2l1.8 1.7 3.2-3.6"/></svg>Developing Tools for Dynamic Speaking</li>
  <li><svg width="12" height="12" viewBox="0 0 12 12" fill="none" stroke="#c9d8e4"><circle cx="6" cy="6" r="5.3"/><path d="M3.5 6.2l1.8 1.7 3.2-3.6"/></svg>Conducting Communication 360° Interviews</li>
  <li><svg width="12" height="12" viewBox="0 0 12 12" fill="none" stroke="#c9d8e4"><circle cx="6" cy="6" r="5.3"/><path d="M3.5 6.2l1.8 1.7 3.2-3.6"/></svg>Sharpening Presentation Skills for Attorneys</li>
</ul>

<div class="abs video" role="img" aria-label="Video still of the coach speaking to camera"></div>
<svg class="abs play" width="44" height="44" viewBox="0 0 44 44" fill="none" stroke="#fff" stroke-width="3"><circle cx="22" cy="22" r="19"/><path d="M17 13l13 9-13 9z" fill="#fff"/></svg>

<footer>
  <div class="abs footer"></div>
  <h2 class="abs footer-name">Clara Brightwell</h2>
  <p class="abs footer-role">Public Speaking Consultant</p>
  <p class="abs footer-about">Providing highly specialized executive coaching services and program design and facilitation for leadership development, public speaking, and all areas of spoken communication.</p>
  <a class="abs btn consult">Consult Now!</a>
  <h2 class="abs call">Call Today. 555.014.2288</h2>
  <p class="abs email">e. info@brightwellvoicetutor.com</p>
  <div class="abs socials footer-socials">
    <i class="social"></i><i class="social on"></i><i class="social"></i><i class="social"></i><i class="social"></i>
  </div>
  <a class="abs btn btn-gold register-foot">Register Now!</a>
  <div class="abs footer-links"><span>Privacy Policy</span><span>|</span><span>Sitemap</span></div>
  <svg class="abs to-top" width="22" height="22" viewBox="0 0 22 22" fill="none" stroke="#fff" stroke-width="2.2" aria-label="Back to top"><path d="M11 20V3M4 10l7-7 7 7"/></svg>
  <div class="abs copyright">© 2019 Brightwell Voice Tutoring.</div>
</footer>

</body>
</html>
```